Automotive component supplier needs a business card design

We need a business card design for our company called Velran Global Components Ltd based in the UK. We are a supplier of interior and exterior components to premium car manufacturers such as Corvel Ashby, Hadley Fenn, Marquist and Tavarelli. We would like to see a modern business card design that uses the colour blue.

Target Market(s)

Premium automotive car manufacturers.

Industry/Entity Type

Automotive

Contact Information for Business Card

Company Name : Velran Global Components Limited
Address: 17 Marlow Yard, Upper Heath, Warwick, CV31 8QL, United Kingdom
Web Address : www.velrancomponents-example.co.uk

Font styles to use
Other font styles liked:
• Helvetica

Colors
3176b5
0255a3
85acd3
cfdeed
cee9f5
85cae6
34a6d7
0692cd
9bcb3c

Requirements
Must have
• Clear company logo and a mixture of blue colours.
Nice to have
• A high quality modern image.
Should not have
• Multiple colours.

```html
<!DOCTYPE html>
<html lang="en">
<head>
<meta charset="utf-8">
<title>Velran Global Components – Business Card</title>
<link href="https://fonts.googleapis.com/css2?family=Lato:wght@400;700&display=swap" rel="stylesheet">
<style>
  :root {
    --brand-blue: #0692cd;
    --deep-blue: #0255a3;
    --accent-green: #9bcb3c;
    --paper: #ffffff;
    --backdrop: #e6e9ec;
    --ink: #2b2b2b;
  }
  * { margin: 0; padding: 0; box-sizing: border-box; }
  html, body { width: 1200px; height: 800px; overflow: hidden; }
  body {
    background: var(--backdrop);
    font-family: "Lato", Helvetica, Arial, sans-serif;
    position: relative;
  }
  .card {
    position: absolute;
    width: 560px;
    height: 320px;
    background: var(--paper);
    box-shadow: 0 6px 18px rgba(0,0,0,0.18);
    overflow: hidden;
  }
  .card--logo { left: 60px; top: 70px; }
  .card--contact { left: 580px; top: 410px; }

  .wordmark {
    position: absolute;
    display: flex;
    align-items: center;
    gap: 12px;
    color: var(--brand-blue);
    font-weight: 700;
    white-space: nowrap;
  }
  .wordmark__square {
    width: 18px; height: 18px;
    background: var(--accent-green);
    flex: none;
  }
  .card--logo .wordmark {
    font-size: 30px;
    left: 50%; top: 118px;
    transform: translateX(-50%);
  }
  .card--logo .web-address {
    position: absolute;
    left: 0; right: 0; top: 238px;
    text-align: center;
    font-size: 13px;
    letter-spacing: 1.5px;
    color: var(--ink);
  }

  .card--contact .wordmark {
    font-size: 27px;
    left: 42px; top: 52px;
  }
  .card-waves { position: absolute; inset: 0; }

  .address {
    position: absolute;
    left: 40px; top: 236px;
    color: var(--paper);
    font-size: 14px;
    line-height: 1.35;
    font-style: normal;
  }
  .person {
    position: absolute;
    left: 296px; top: 172px;
    color: var(--paper);
  }
  .person__name {
    color: var(--accent-green);
    font-size: 19px;
    font-weight: 700;
  }
  .person__role { font-size: 13px; margin-top: 2px; }
  .contact-list {
    list-style: none;
    margin-top: 10px;
    font-size: 12.5px;
  }
  .contact-list li {
    display: flex;
    align-items: center;
    gap: 8px;
    height: 18px;
  }
  .contact-list svg { width: 11px; height: 11px; flex: none; }
</style>
</head>
<body>

  <section class="card card--logo" aria-label="Business card, logo side">
    <div class="wordmark"><span class="wordmark__square"></span>Velran Global Components</div>
    <p class="web-address">www.velrancomponents-example.co.uk</p>
  </section>

  <section class="card card--contact" aria-label="Business card, contact side">
    <svg class="card-waves" viewBox="0 0 560 320" aria-hidden="true">
      <path d="M0,196 C160,206 300,180 400,120 C470,78 520,58 560,50 L560,320 L0,320 Z" fill="var(--brand-blue)"/>
      <path d="M0,180 C160,192 300,166 400,107 C470,66 520,46 560,38" fill="none" stroke="var(--accent-green)" stroke-width="7"/>
      <path d="M0,168 C160,178 300,152 400,94 C470,55 520,35 560,27" fill="none" stroke="var(--brand-blue)" stroke-width="3"/>
    </svg>

    <div class="wordmark"><span class="wordmark__square"></span>Velran Global Components</div>

    <address class="address">
      17 Marlow Yard, Upper Heath<br>
      Warwick, CV31 8QL<br>
      United Kingdom
    </address>

    <div class="person">
      <p class="person__name">Maren Holloway</p>
      <p class="person__role">Manager</p>
      <ul class="contact-list">
        <li>
          <svg viewBox="0 0 12 12"><path d="M2,1 L4,1 L5,4 L3.6,5 C4.3,6.6 5.4,7.7 7,8.4 L8,7 L11,8 L11,10 C11,10.6 10.6,11 10,11 C5,11 1,7 1,2 C1,1.4 1.4,1 2,1 Z" fill="var(--accent-green)"/></svg>
          512 004 2790
        </li>
        <li>
          <svg viewBox="0 0 12 12"><rect x="3" y="0.5" width="6" height="11" rx="1" fill="none" stroke="var(--accent-green)" stroke-width="1.2"/><circle cx="6" cy="9.5" r="0.8" fill="var(--accent-green)"/></svg>
          512 004 2791
        </li>
        <li>
          <svg viewBox="0 0 12 12"><rect x="0.5" y="2.5" width="11" height="7" fill="var(--accent-green)"/><path d="M0.5,2.5 L6,6.5 L11.5,2.5" fill="none" stroke="var(--brand-blue)" stroke-width="1"/></svg>
          info@velrancomponents-example.co.uk
        </li>
        <li>
          <svg viewBox="0 0 12 12"><circle cx="6" cy="6" r="5" fill="none" stroke="var(--accent-green)" stroke-width="1.2"/><path d="M1,6 L11,6 M6,1 C3.5,4 3.5,8 6,11 M6,1 C8.5,4 8.5,8 6,11" fill="none" stroke="var(--accent-green)" stroke-width="1"/></svg>
          www.velrancomponents-example.co.uk
        </li>
      </ul>
    </div>
  </section>

</body>
</html>
```